Counseling Practice Business Card

I need a professional looking business card incorporating my new logo that was just completed. Card needs to incorporate my name and title, description of my specialty, my address, my phone number, my fax number, my email and my website URL. I need to be able to choose design on/with different paper colors and textures.
I do not have a lot of business card ideas so I am open to anything but I want bold,sharp, clear card without additional designs other than my logo (see attached file info). I am open to different color backgrounds or paper colors including black. I do not like traditional brackets around area codes in phone number or dashes between numbers in phone number. Am open to other ways of presenting including periods between numbers as appropriate. I do not know enough to know what I like yet but I want card to coordinate and work together with my logo. My practice emphasizes natural mental health interventions so any use of color (with background paper color or the blue and green in my logo) that elicits nature is nice. In addition to black, any natural brown or wood looking background might be desirable also. Most of the offerings so far look very similar and boring.

Target Market(s)

Potential therapy clients and other professionals

Contact Information for Business Card

Card information:
Gerald M. Whitcombe, Ph.D.
Licensed Clinical Psychologist
Integrative Health Coach
4812 Marlowe Ridge Blvd SE
Suite 310
Alder Falls, GA 30412
(770) 415-2983 phone
(770) 581-4096 fax
drgeraldwhitcombe@quillmarsh.net
brightfernwellness.net

Font styles to use
Serif
Sans Serif
Other font styles liked:
• anything that you think looks crisp, clear and easily readable

Requirements
Must have
• Any color used should coordinate with my logo design (see attached files).
• Card should be printed horizontally so top and bottom are longest sides of rectangle.
• Background color or paper color should complement and highlight logo. Do not like a white background. black, grey, brown or any color my logo would blend well with.
Nice to have
• I would like designer to utilize color to highlight letters/name or phone-fax-web symbols.
• Bottom edge of card could be highlighted if appropriate to an idea.
Should not have
• I would NOT want the card to have a pure white background at all.
• No clear cards.
• Cards should be oriented with long sides on bottom and top, NOT sides. DO NOT LIKE THIS THIN TALL ORIENTATION.

```html
<!DOCTYPE html>
<html lang="en">
<head>
<meta charset="utf-8">
<title>Brightfern Wellness – Business Card</title>
<link href="https://fonts.googleapis.com/css2?family=Open+Sans:wght@400;600;700&display=swap" rel="stylesheet">
<style>
  :root{
    --backdrop:#e9e4de;
    --paper:#bc9375;
    --brand-blue:#2a7cc4;
    --brand-green:#1e7d3a;
    --ink-light:#fdf8f3;
    --rule:rgba(255,255,255,0.55);
  }
  *{margin:0;padding:0;box-sizing:border-box}
  html,body{width:1200px;height:840px;overflow:hidden;background:var(--backdrop);font-family:"Open Sans",Arial,sans-serif}
  .stage{position:relative;width:1200px;height:840px}
  .card{position:absolute;left:340px;width:520px;height:297px;background:var(--paper);box-shadow:0 6px 18px rgba(60,40,20,0.25);overflow:hidden}
  .card--front{top:103px}
  .card--back{top:440px}
  .brand{position:absolute;display:flex;align-items:center;gap:10px;color:var(--brand-blue);font-weight:600;line-height:1.05}
  .brand__dot{width:14px;height:14px;border-radius:50%;background:var(--brand-blue);flex:none}
  .brand__name{font-size:30px;letter-spacing:0.5px}
  .brand__sub{display:block;font-size:15px;letter-spacing:5px;text-transform:uppercase}
  .card--front .brand{left:0;right:0;top:112px;justify-content:center}
  .edge{position:absolute;top:0;bottom:0;width:8px}
  .edge--left{left:0;background:var(--brand-blue)}
  .edge--right{right:0;background:var(--brand-green)}
  .card--back .brand{left:32px;top:176px}
  .card--back .brand__name{font-size:26px}
  .card--back .brand__sub{font-size:13px;letter-spacing:4px}
  .divider{position:absolute;left:252px;top:28px;bottom:34px;width:1px;background:var(--rule)}
  .details{position:absolute;left:268px;top:28px;right:18px;color:var(--ink-light);font-size:11.5px;line-height:1.45}
  .details__name{color:var(--brand-blue);font-weight:700;font-size:13px;text-transform:uppercase;letter-spacing:0.3px}
  .details__title{color:var(--brand-green);font-weight:600;font-size:12px}
  .details__address{margin-top:8px}
  .contacts{list-style:none;margin-top:6px}
  .contacts li{display:flex;align-items:center;gap:7px;margin-bottom:1px}
  .contacts svg{width:13px;height:13px;flex:none}
</style>
</head>
<body>
<main class="stage">
  <section class="card card--front" aria-label="Card front">
    <div class="brand">
      <span class="brand__dot"></span>
      <span class="brand__name">Brightfern<span class="brand__sub">Wellness</span></span>
    </div>
  </section>

  <section class="card card--back" aria-label="Card back">
    <div class="edge edge--left"></div>
    <div class="edge edge--right"></div>
    <div class="brand">
      <span class="brand__dot"></span>
      <span class="brand__name">Brightfern<span class="brand__sub">Wellness</span></span>
    </div>
    <div class="divider"></div>
    <div class="details">
      <p class="details__name">Gerald M. Whitcombe, Ph.D.</p>
      <p class="details__title">Licensed Clinical Psychologist</p>
      <p class="details__title">Integrative Health Coach</p>
      <p class="details__address">4812 Marlowe Ridge Blvd SE<br>Suite 310<br>Alder Falls, GA 30412</p>
      <ul class="contacts">
        <li>
          <svg viewBox="0 0 14 14" aria-hidden="true"><circle cx="7" cy="7" r="7" fill="var(--brand-blue)"/><path d="M4.3 3.5l1.4 0 .6 1.8-.9.7a5 5 0 0 0 2.6 2.6l.7-.9 1.8.6v1.4c0 .4-.3.7-.7.7A6.3 6.3 0 0 1 3.6 4.2c0-.4.3-.7.7-.7z" fill="#fff"/></svg>
          <span>(770) 415-2983</span>
        </li>
        <li>
          <svg viewBox="0 0 14 14" aria-hidden="true"><circle cx="7" cy="7" r="7" fill="var(--brand-blue)"/><rect x="4" y="3.3" width="6" height="2.6" fill="#fff"/><rect x="3.2" y="6.3" width="7.6" height="3.4" rx="0.5" fill="#fff"/><rect x="4.5" y="9" width="5" height="1.8" fill="#fff"/></svg>
          <span>(770) 581-4096</span>
        </li>
        <li>
          <svg viewBox="0 0 14 14" aria-hidden="true"><circle cx="7" cy="7" r="7" fill="var(--brand-blue)"/><rect x="3.3" y="4.4" width="7.4" height="5.2" fill="#fff"/><path d="M3.3 4.4L7 7.4l3.7-3" fill="none" stroke="var(--brand-blue)" stroke-width="0.8"/></svg>
          <span>drgeraldwhitcombe@quillmarsh.net</span>
        </li>
        <li>
          <svg viewBox="0 0 14 14" aria-hidden="true"><circle cx="7" cy="7" r="7" fill="var(--brand-blue)"/><g fill="none" stroke="#fff" stroke-width="0.8"><circle cx="7" cy="7" r="3.6"/><ellipse cx="7" cy="7" rx="1.6" ry="3.6"/><path d="M3.4 7h7.2"/></g></svg>
          <span>www.brightfernwellness.net</span>
        </li>
      </ul>
    </div>
  </section>
</main>
</body>
</html>
```